Corporate Business Card

Very professional, Modern, Not to busy, include phone address email, website
(253) 617-4930, 18761 52nd Avenue S, Kent, WA 98047, martin@plumlinegroup.com, varkoworks.com

Target Market(s)

Manufacturing

Industry/Entity Type

Aero, machining, manufacturing, Off road racing

Contact Information for Business Card

Phone, address email, website

```html
<!DOCTYPE html>
<html lang="en">
<head>
<meta charset="utf-8">
<title>Varko Works – Business Card</title>
<link rel="stylesheet" href="https://fonts.googleapis.com/css2?family=Montserrat:wght@400;500;700&display=swap">
<style>
  :root {
    --page-bg: #ecebe8;
    --card-bg: #ffffff;
    --navy: #1e3d7b;
    --red: #d5262f;
    --ink: #1b1b1b;
    --card-w: 600px;
    --card-h: 343px;
  }
  * { box-sizing: border-box; margin: 0; padding: 0; }
  html, body { width: 1200px; height: 1023px; overflow: hidden; }
  body {
    background: var(--page-bg);
    font-family: "Montserrat", sans-serif;
    color: var(--ink);
    position: relative;
  }
  .card {
    position: absolute;
    left: 300px;
    width: var(--card-w);
    height: var(--card-h);
    background: var(--card-bg);
    border-radius: 22px;
    box-shadow: 0 6px 18px rgba(0,0,0,0.18);
    overflow: hidden;
  }
  .card--front { top: 112px; }
  .card--back { top: 568px; }
  .card__frame {
    position: absolute;
    inset: 24px;
    border: 1.5px solid var(--red);
    border-radius: 18px;
  }
  .brand {
    position: absolute;
    display: flex;
    align-items: center;
    gap: 12px;
  }
  .brand__mark {
    width: 16px; height: 16px;
    background: var(--navy);
    flex: none;
  }
  .brand__name {
    font-weight: 700;
    color: var(--navy);
    letter-spacing: 0.02em;
    white-space: nowrap;
    line-height: 1;
  }
  .brand__rule {
    position: absolute;
    height: 2px;
    background: var(--navy);
  }
  .card--front .brand { left: 140px; top: 138px; }
  .card--front .brand__name { font-size: 38px; }
  .card--front .brand__rule { left: 140px; top: 200px; width: 170px; }

  .card--back .brand { left: 282px; top: 62px; gap: 10px; }
  .card--back .brand__mark { width: 12px; height: 12px; }
  .card--back .brand__name { font-size: 27px; }
  .card--back .brand__rule { left: 282px; top: 108px; width: 120px; }

  .address {
    position: absolute;
    left: 58px;
    top: 128px;
    font-size: 15px;
    font-weight: 500;
    line-height: 1.45;
  }
  .contacts {
    position: absolute;
    left: 58px;
    bottom: 46px;
    list-style: none;
    font-size: 15px;
    font-weight: 500;
  }
  .contacts li {
    display: flex;
    align-items: center;
    gap: 10px;
    line-height: 1.75;
  }
  .contacts svg { width: 15px; height: 15px; fill: var(--red); flex: none; }
</style>
</head>
<body>

<section class="card card--front" aria-label="Card front">
  <div class="card__frame"></div>
  <div class="brand">
    <span class="brand__mark"></span>
    <span class="brand__name">VARKO WORKS</span>
  </div>
  <div class="brand__rule"></div>
</section>

<section class="card card--back" aria-label="Card back">
  <div class="card__frame"></div>
  <div class="brand">
    <span class="brand__mark"></span>
    <span class="brand__name">VARKO WORKS</span>
  </div>
  <div class="brand__rule"></div>

  <p class="address">18761 52nd Avenue<br>S, Kent, WA 98047</p>

  <ul class="contacts">
    <li>
      <svg viewBox="0 0 24 24" aria-hidden="true"><path d="M6.6 10.8a15.1 15.1 0 0 0 6.6 6.6l2.2-2.2c.3-.3.7-.4 1-.2 1.1.4 2.3.6 3.6.6.6 0 1 .4 1 1V20c0 .6-.4 1-1 1A17 17 0 0 1 3 4c0-.6.4-1 1-1h3.5c.6 0 1 .4 1 1 0 1.3.2 2.5.6 3.6.1.3 0 .7-.2 1z"/></svg>
      <span>(253) 617-4930</span>
    </li>
    <li>
      <svg viewBox="0 0 24 24" aria-hidden="true"><path d="M2 5h20v14H2z M2 5l10 8 10-8" stroke="#fff" stroke-width="1.5"/></svg>
      <span>martin@plumlinegroup.com</span>
    </li>
    <li>
      <svg viewBox="0 0 24 24" aria-hidden="true"><circle cx="12" cy="12" r="10"/><path d="M2 12h20M12 2c3 3 3 17 0 20M12 2c-3 3-3 17 0 20" stroke="#fff" stroke-width="1.3" fill="none"/></svg>
      <span>www.varkoworks.com</span>
    </li>
  </ul>
</section>

</body>
</html>
```